BUSINESS CARD - HALLORAN FIELD SERVICES

I would like to create a business card for my fertilizer spreading business. I would like to incorporate my existing logo and also a description of the services offered. The business card will be given to farmers so must be kept simple but effective. It will also be left in stores so much also be eye catching in order to stand out from other cards.

Target Market(s)

FARMERS

Requirements
Must have
• FRONT OF CARD = EXISTING LOGO + "CUSTOMISED SPREADING" below the logo

REAR Of CARD = SERVICES OFFERED AND CONTACT DETAILS

- Bulk fertilizer including Lime, Gypsum, Manure & Compost
- Granular fertilizer including Single Super, Urea, Gran-am, & Custom Blends
- Modern equipment - Autosteer & Variable Rate Capable
- Friendly & Reliable Service
- Contact Gus: 0417 552 308
Nice to have
• utilize same color scheme as existing logo

```html
<!DOCTYPE html>
<html lang="en">
<head>
<meta charset="utf-8">
<title>Halloran Field Services – Business Card</title>
<link href="https://fonts.googleapis.com/css2?family=Lato:ital,wght@0,300;0,400;0,700;0,900;1,400&display=swap" rel="stylesheet">
<style>
  :root {
    --backdrop: #6e6f71;
    --card-white: #ffffff;
    --charcoal: #58585a;
    --charcoal-deep: #4a4a4c;
    --orange: #f7941d;
    --text-light: #e8e8e8;
    --white: #ffffff;
  }
  * { margin: 0; padding: 0; box-sizing: border-box; }
  html, body {
    width: 1200px; height: 1200px; overflow: hidden;
    background: var(--backdrop);
    font-family: "Lato", sans-serif;
  }
  .card {
    position: absolute; left: 184px; width: 840px;
    box-shadow: 0 10px 24px rgba(0,0,0,0.35);
    overflow: hidden;
  }
  /* Front */
  .card-front { top: 103px; height: 477px; background: var(--card-white); }
  .brand {
    position: absolute; top: 40px; left: 0; right: 0;
    display: flex; flex-direction: column; align-items: center;
  }
  .brand-disc {
    width: 180px; height: 180px; border-radius: 50%;
    background: var(--charcoal);
  }
  .brand-name {
    margin-top: 26px;
    font-weight: 700; font-size: 46px; letter-spacing: 0.5px;
    color: var(--charcoal); text-transform: uppercase;
  }
  .grass-band {
    position: absolute; left: 0; right: 0; top: 361px; height: 44px;
    background: linear-gradient(to bottom, rgba(247,148,29,0) 0%, rgba(247,148,29,0.6) 45%, var(--orange) 100%);
  }
  .tagline-band {
    position: absolute; left: 0; right: 0; top: 404px; height: 73px;
    background: var(--orange);
    display: flex; align-items: center; justify-content: center;
  }
  .tagline {
    color: var(--white); font-weight: 700; font-size: 44px; letter-spacing: 0.5px;
  }
  /* Back */
  .card-back { top: 629px; height: 480px; background: var(--charcoal); }
  .back-brand {
    position: absolute; top: 26px; right: 26px;
    display: flex; flex-direction: column; align-items: center;
  }
  .back-brand-disc {
    width: 70px; height: 70px; border-radius: 50%; background: var(--white);
  }
  .back-brand-name {
    margin-top: 8px; color: var(--white);
    font-weight: 700; font-size: 17px; text-transform: uppercase; letter-spacing: 0.3px;
  }
  .services {
    position: absolute; left: 158px; top: 178px; list-style: none;
  }
  .services-title {
    position: absolute; left: 190px; top: 160px;
    color: var(--white); font-weight: 700; font-size: 28px;
  }
  .services { top: 222px; }
  .service { position: relative; padding-left: 32px; margin-bottom: 9px; }
  .service-bullet {
    position: absolute; left: 2px; top: 5px; width: 22px; height: 12px;
  }
  .service-name {
    color: var(--orange); font-weight: 700; font-size: 18px; text-transform: uppercase;
  }
  .service-name em { font-style: italic; font-weight: 400; text-transform: none; font-size: 16px; }
  .service-detail { color: var(--text-light); font-weight: 300; font-size: 16.5px; margin-top: 2px; }
  .contact-band {
    position: absolute; left: 0; right: 0; top: 420px; height: 60px;
    background: var(--orange);
    display: flex; align-items: center; padding-left: 150px;
  }
  .phone-icon {
    width: 40px; height: 40px; border-radius: 50%; background: var(--charcoal-deep);
    display: flex; align-items: center; justify-content: center; margin-right: 14px;
  }
  .contact-text { color: var(--white); font-weight: 700; font-size: 33px; }
</style>
</head>
<body>
  <section class="card card-front">
    <div class="brand">
      <div class="brand-disc"></div>
      <div class="brand-name">Halloran Field Services</div>
    </div>
    <div class="grass-band" role="img" aria-label="Orange silhouette of grass and crops along the bottom edge"></div>
    <div class="tagline-band"><span class="tagline">CUSTOMISED SPREADING</span></div>
  </section>

  <section class="card card-back">
    <div class="back-brand">
      <div class="back-brand-disc"></div>
      <div class="back-brand-name">Halloran Field Services</div>
    </div>

    <h2 class="services-title">Services Offered:</h2>
    <ul class="services">
      <li class="service">
        <svg class="service-bullet" viewBox="0 0 22 12"><path d="M2 2 L11 10 L20 2" fill="none" stroke="#f7941d" stroke-width="3" stroke-linecap="round" stroke-linejoin="round"/></svg>
        <div class="service-name">Bulk Fertilizer <em>including</em></div>
        <div class="service-detail">Lime, Gypsum, Manure &amp; Compost</div>
      </li>
      <li class="service">
        <svg class="service-bullet" viewBox="0 0 22 12"><path d="M2 2 L11 10 L20 2" fill="none" stroke="#f7941d" stroke-width="3" stroke-linecap="round" stroke-linejoin="round"/></svg>
        <div class="service-name">Modern Equipment</div>
        <div class="service-detail">Autosteer &amp; Variable Rate Capable</div>
      </li>
      <li class="service">
        <svg class="service-bullet" viewBox="0 0 22 12"><path d="M2 2 L11 10 L20 2" fill="none" stroke="#f7941d" stroke-width="3" stroke-linecap="round" stroke-linejoin="round"/></svg>
        <div class="service-name">Granular Fertilizer <em>including</em></div>
        <div class="service-detail">Single Super, Urea, Gran-am, &amp; Custom Blends</div>
      </li>
      <li class="service">
        <svg class="service-bullet" viewBox="0 0 22 12"><path d="M2 2 L11 10 L20 2" fill="none" stroke="#f7941d" stroke-width="3" stroke-linecap="round" stroke-linejoin="round"/></svg>
        <div class="service-name">Friendly &amp; Reliable Services</div>
      </li>
    </ul>

    <div class="contact-band">
      <div class="phone-icon">
        <svg width="22" height="22" viewBox="0 0 24 24" aria-hidden="true"><path fill="#ffffff" d="M6.6 10.8a15.1 15.1 0 0 0 6.6 6.6l2.2-2.2a1 1 0 0 1 1-.25 11.4 11.4 0 0 0 3.6.57 1 1 0 0 1 1 1V20a1 1 0 0 1-1 1A17 17 0 0 1 3 4a1 1 0 0 1 1-1h3.5a1 1 0 0 1 1 1c0 1.25.2 2.45.57 3.6a1 1 0 0 1-.25 1z"/></svg>
      </div>
      <span class="contact-text">GUS: 0417 552 308</span>
    </div>
  </section>
</body>
</html>
```